Black Matte card with samurai logo which I would like it to be textured and company name on one side and on the other side I would like the company information with the reno (Face logo) Sushi logo. Double Sided card.

majority customers are University students, University sororities and fraternities.

It Company

Reno Sushi
317 W. Harlow Ave
Tucson, AZ 85042
Phone (520)413-6271
Fax (520)357-1846
E-mail: Renosushidesert@mailbox-example.com
FB: Renosushidesert
Twitter: Renosushidesert

• Present Normal

```html
<!DOCTYPE html>
<html lang="en">
<head>
<meta charset="utf-8">
<title>Reno Sushi — Business Card</title>
<link rel="stylesheet" href="https://fonts.googleapis.com/css2?family=Open+Sans:wght@400;600&display=swap">
<style>
  :root {
    --backdrop: #e9e6e1;
    --matte-black: #1b1b1b;
    --matte-black-light: #2a2a2a;
    --band-black: #231f20;
    --paper: #ffffff;
    --sushi-red: #a8322b;
    --ink-white: #ffffff;
    --ink-dark: #2b2b2b;
    --divider: #6b6b6b;
  }
  * { box-sizing: border-box; margin: 0; padding: 0; }
  html, body {
    width: 1200px; height: 987px; overflow: hidden;
    background: var(--backdrop);
    font-family: "Open Sans", Arial, sans-serif;
  }
  .canvas { position: relative; width: 1200px; height: 987px; }

  .card {
    position: absolute;
    width: 764px; height: 438px;
    box-shadow: 0 3px 10px rgba(0,0,0,0.25);
    overflow: hidden;
  }

  /* Front */
  .card-front {
    left: 41px; top: 37px;
    background: radial-gradient(circle at 50% 40%, var(--matte-black-light), var(--matte-black) 75%);
  }
  .front-mark {
    position: absolute; left: 0; right: 0; top: 150px;
    display: flex; align-items: center; justify-content: center; gap: 18px;
  }
  .front-mark .sun { width: 34px; height: 34px; border-radius: 50%; background: var(--sushi-red); }
  .front-mark .brand-name {
    color: var(--ink-white); font-size: 58px; font-weight: 600; letter-spacing: 1px;
  }
  .website {
    position: absolute; left: 0; right: 0; top: 366px;
    text-align: center; color: var(--ink-white);
    font-size: 21px; letter-spacing: 2.5px;
  }

  /* Back */
  .card-back { left: 378px; top: 521px; background: var(--paper); }
  .back-mark {
    position: absolute; left: 0; right: 0; top: 80px;
    display: flex; flex-direction: column; align-items: center; gap: 14px;
  }
  .back-mark .sun { width: 26px; height: 26px; border-radius: 50%; background: var(--sushi-red); }
  .back-mark .brand-name { color: var(--sushi-red); font-size: 48px; font-weight: 400; }
  .red-rule {
    position: absolute; left: 0; right: 0; top: 268px; height: 4px; background: var(--sushi-red);
  }
  .info-band {
    position: absolute; left: 0; right: 0; top: 279px; bottom: 0; background: var(--band-black);
    color: var(--ink-white); font-size: 18px;
  }
  .address {
    position: absolute; right: 428px; top: 40px; text-align: right; line-height: 29px;
    font-style: normal;
  }
  .band-divider {
    position: absolute; left: 352px; top: 10px; bottom: 14px; width: 1px; background: var(--divider);
  }
  .contacts {
    position: absolute; left: 370px; top: 8px; list-style: none; line-height: 29px;
  }
  .contacts li { display: flex; align-items: center; gap: 9px; }
  .contacts .icon { width: 17px; height: 17px; flex: none; }
  .contacts .social-square { width: 16px; height: 16px; background: #8a9bb4; border-radius: 2px; flex: none; }
</style>
</head>
<body>
<main class="canvas">
  <section class="card card-front" aria-label="Card front">
    <div class="front-mark">
      <span class="sun"></span>
      <span class="brand-name">Reno Sushi</span>
    </div>
    <p class="website">www.renosushidesert.com</p>
  </section>

  <section class="card card-back" aria-label="Card back">
    <div class="back-mark">
      <span class="sun"></span>
      <span class="brand-name">Reno Sushi</span>
    </div>
    <div class="red-rule"></div>
    <div class="info-band">
      <address class="address">
        Reno Sushi 317<br>
        W. Harlow Ave Tucson<br>
        AZ 85042
      </address>
      <div class="band-divider"></div>
      <ul class="contacts">
        <li>
          <svg class="icon" viewBox="0 0 24 24" aria-hidden="true"><path fill="#fff" d="M6.6 10.8a15 15 0 0 0 6.6 6.6l2.2-2.2c.3-.3.7-.4 1-.2 1.1.4 2.3.6 3.6.6.6 0 1 .4 1 1V20c0 .6-.4 1-1 1A17 17 0 0 1 3 4c0-.6.4-1 1-1h3.5c.6 0 1 .4 1 1 0 1.3.2 2.5.6 3.6.1.3 0 .7-.2 1z"/></svg>
          <span>(520)413-6271</span>
        </li>
        <li>
          <svg class="icon" viewBox="0 0 24 24" aria-hidden="true"><rect x="7" y="2" width="10" height="20" rx="2" fill="#fff"/><rect x="9" y="5" width="6" height="7" fill="#231f20"/></svg>
          <span>(520)357-1846</span>
        </li>
        <li>
          <svg class="icon" viewBox="0 0 24 24" aria-hidden="true"><rect x="2" y="5" width="20" height="14" rx="1" fill="#fff"/><path d="M2 6l10 7 10-7" stroke="#231f20" stroke-width="1.6" fill="none"/></svg>
          <span>Renosushidesert@mailbox-example.com</span>
        </li>
        <li><span class="social-square"></span><span>Renosushidesert</span></li>
        <li><span class="social-square"></span><span>Renosushidesert</span></li>
      </ul>
    </div>
  </section>
</main>
</body>
</html>
```